International Dental Education Website

This project is for a small teaching center on endodontic and micro dentistry in Norway. We need a Wordpress website design to display and highlight dental educational courses. Please use our new logo - see attached file. We like lighter, pastel oriented colors. The following sites are nicely laid out and you can use these as a guideline of sorts but I do want a unique site.
http://vorplaxe.example/en, http://www.trelvanmork.example/Education.aspx?currentSection=courses&cid=14,
http://www.quastifel.example/.
Please create a space for a possible video on the home page. Please include a small contact form on the home page(name, email, phone, text box). Would like a horizonatal naviagtion bar. Would like an image to go across the whole top part of the site and this may rotate. Please use a stock image that shows a classroom type setting. Put phone number at the top of the screen. Put address and sitemap in a footer.

Reason: Upcoming vacation with limited internet access. Please continue to submit any designs. Thanks you.

Reason: The client is from a foreign country and is on an extended vacation.

Target Market(s)

General dentists (GPs) and specialists in Endodontics

Industry/Entity Type

Dental

Requirements
Must have
• Sitemap: HOME, COURSES, LECTURER, CONTACT US,
NORWEGIAN/ENGLISH. Phone number is: +47 53169027. Business name and address: Mivo Lark AS, Endodontic Teaching Center,
Tollbeks vei 41C, 0397 Oslo, Norway.

```html
<!DOCTYPE html>
<html lang="en">
<head>
<meta charset="utf-8">
<title>Mivo Lark – Endodontic Teaching Center</title>
<link rel="stylesheet" href="https://fonts.googleapis.com/css2?family=Ubuntu:wght@300;400;500&display=swap">
<style>
:root{
  --teal:#67bcc2;
  --teal-dark:#4ea6ad;
  --teal-light:#8fd0d4;
  --heading:#6b7f88;
  --text:#3d3d3d;
  --muted:#8a979d;
  --rule:#d5d9db;
  --band:#95a5ad;
  --white:#ffffff;
  --field:#b9c1c5;
}
*{box-sizing:border-box;margin:0;padding:0}
html,body{width:1200px;height:1064px;overflow:hidden;background:var(--white)}
body{font-family:"Ubuntu",Arial,sans-serif;color:var(--text);position:relative}
.page{position:relative;width:1200px;height:1064px;overflow:hidden}

.lang-switch{position:absolute;top:10px;right:40px;font-size:13px;color:var(--heading);display:flex;gap:6px;align-items:center;text-transform:uppercase}
.lang-switch .flag{display:inline-block;width:17px;height:11px;vertical-align:middle;margin-right:3px}
.lang-switch .sep{color:var(--muted)}
.top-phone{position:absolute;top:39px;right:40px;font-size:17px;color:var(--heading)}
.top-phone strong{font-weight:500}

.brand{position:absolute;left:22px;top:40px;display:flex;align-items:center;gap:10px}
.brand-mark{width:22px;height:22px;border-radius:50%;background:var(--teal)}
.brand-name{font-size:40px;font-weight:500;color:var(--teal);letter-spacing:-0.5px}

.main-nav{position:absolute;top:94px;right:30px;display:flex;height:33px}
.main-nav a{display:flex;align-items:center;padding:0 18px;font-size:15px;color:var(--heading);text-decoration:none;text-transform:uppercase;border-right:1px solid var(--rule)}
.main-nav a.active{background:linear-gradient(var(--teal-light),var(--teal-dark));color:var(--white);padding:0 20px;border-right:none}
.main-nav a:nth-child(2){padding:0 20px}

.hero{position:absolute;left:22px;top:130px;width:1149px;height:390px;background:linear-gradient(100deg,#cfd9de 0%,#e9d2c1 30%,#e3c2a8 55%,#cfdceb 80%,#e3ecf6 100%)}

.welcome{position:absolute;left:21px;top:543px;width:362px}
.section-title{font-size:28px;font-weight:300;color:var(--heading);margin-bottom:8px}
.welcome p{font-size:14.5px;line-height:21px;color:var(--text)}
.read-more{position:absolute;right:0;top:272px;font-size:12.5px;color:var(--muted);text-decoration:none}

.divider{position:absolute;top:545px;width:1px;height:298px;background:var(--rule)}
.divider.one{left:408px}
.divider.two{left:815px}

.video{position:absolute;left:428px;top:553px;width:365px;height:273px}

.quick-contact{position:absolute;left:836px;top:543px;width:310px}
.contact-form{margin-left:30px;margin-top:10px;width:277px}
.contact-form label{display:block;font-size:14px;color:var(--text);margin-bottom:3px}
.contact-form .field{display:block;width:277px;height:25px;border:1px solid var(--field);background:var(--white);margin-bottom:12px}
.contact-form textarea.field{height:68px;resize:none;margin-bottom:2px}
.contact-form .submit{display:block;margin-left:auto;width:83px;height:26px;border:none;background:linear-gradient(var(--teal-light),var(--teal-dark));color:var(--white);font-family:inherit;font-size:14px}

.footer-rule{position:absolute;left:22px;top:888px;width:1149px;height:1px;background:var(--rule)}
.footer-links{position:absolute;top:904px;list-style:none}
.footer-links li{font-size:11px;line-height:28px;text-transform:uppercase}
.footer-links a{color:var(--heading);text-decoration:none}
.footer-links.sitemap{left:41px}
.footer-links.policies{left:254px;top:907px}
.footer-contact{position:absolute;left:750px;top:951px;font-size:13px;line-height:20px;color:var(--heading)}
.footer-address{position:absolute;left:983px;top:907px}
.footer-address h3{font-size:16px;font-weight:400;color:var(--heading);margin-bottom:4px}
.footer-address p{font-size:12px;line-height:20px;color:var(--text);padding-left:3px}

.copyright{position:absolute;left:22px;top:1015px;width:1149px;height:40px;background:var(--band);color:var(--white);font-size:11px;display:flex;align-items:center;justify-content:center}
</style>
</head>
<body>
<div class="page">
  <header>
    <div class="lang-switch">
      <span><svg class="flag" viewBox="0 0 17 11"><rect width="17" height="11" fill="#c8202f"/><rect x="5" width="3" height="11" fill="#fff"/><rect y="4" width="17" height="3" fill="#fff"/><rect x="5.8" width="1.4" height="11" fill="#1f3a78"/><rect y="4.8" width="17" height="1.4" fill="#1f3a78"/></svg>Norwegian</span>
      <span class="sep">|</span>
      <span><svg class="flag" viewBox="0 0 17 11"><rect width="17" height="11" fill="#23377a"/><rect x="7" width="3" height="11" fill="#fff"/><rect y="4" width="17" height="3" fill="#fff"/><rect x="7.7" width="1.6" height="11" fill="#c8202f"/><rect y="4.7" width="17" height="1.6" fill="#c8202f"/></svg>English</span>
    </div>
    <div class="top-phone">Call : <strong>+47 53169027</strong></div>
    <div class="brand">
      <span class="brand-mark"></span>
      <span class="brand-name">Mivo Lark</span>
    </div>
    <nav class="main-nav">
      <a class="active" href="#">Home</a>
      <a href="#">Courses</a>
      <a href="#">Lecturer</a>
      <a href="#">Contact Us</a>
    </nav>
  </header>

  <div class="hero" role="img" aria-label="Rotating banner photo of a smiling family of four against a pale blue sky"></div>

  <section class="welcome">
    <h2 class="section-title">Welcome to Mivo Lark</h2>
    <p>Lorem Ipsum is simply dummy text of the printing and typesetting industry. Lorem Ipsum has been the industry's standard dummy text ever since the 1500s, when an unknown printer took a galley of type and scrambled it to make a type specimen book. It has survived not only five centuries, but also the leap into electronic typesetting, remaining essentially unchanged. It was popularised in the 1960s with the release of Letraset sheets containing Lorem Ipsum passages, and more recently with desktop</p>
    <a class="read-more" href="#">Read More</a>
  </section>

  <div class="divider one"></div>

  <svg class="video" viewBox="0 0 365 273" aria-label="Video player">
    <rect width="365" height="273" fill="#000"/>
    <circle cx="182" cy="126" r="26" fill="#2a2a2a" stroke="#9a9a9a" stroke-width="3"/>
    <path d="M175 113 L194 126 L175 139 Z" fill="#cfcfcf"/>
    <rect y="256" width="365" height="17" fill="#3a3f44"/>
    <rect x="5" y="260" width="9" height="9" fill="#9aa3a8"/>
    <circle cx="29" cy="264.5" r="5" fill="#9aa3a8"/>
    <path d="M27 261.5 L32 264.5 L27 267.5 Z" fill="#3a3f44"/>
    <rect x="40" y="263" width="200" height="3" fill="#6b7278"/>
    <circle cx="42" cy="264.5" r="2.5" fill="#ddd"/>
    <rect x="246" y="259" width="52" height="11" fill="#1f5b74"/>
    <text x="272" y="267.5" font-size="8" fill="#dfe8ec" text-anchor="middle" font-family="Ubuntu, sans-serif">00:00 28:30</text>
    <path d="M305 262 h3 l4 -3 v11 l-4 -3 h-3 Z" fill="#9aa3a8"/>
    <rect x="318" y="263" width="30" height="3" fill="#6b7278"/>
    <rect x="353" y="259" width="8" height="10" fill="#9aa3a8"/>
  </svg>

  <div class="divider two"></div>

  <section class="quick-contact">
    <h2 class="section-title">Quick Contact</h2>
    <form class="contact-form">
      <label for="qc-name">Name</label>
      <input class="field" id="qc-name" type="text">
      <label for="qc-email">E mail ID</label>
      <input class="field" id="qc-email" type="email">
      <label for="qc-phone">Phone No.</label>
      <input class="field" id="qc-phone" type="tel">
      <label for="qc-msg">Message</label>
      <textarea class="field" id="qc-msg"></textarea>
      <button class="submit" type="submit">Submit</button>
    </form>
  </section>

  <footer>
    <div class="footer-rule"></div>
    <ul class="footer-links sitemap">
      <li><a href="#">Home</a></li>
      <li><a href="#">Courses</a></li>
      <li><a href="#">Lecturer</a></li>
      <li><a href="#">Contact Us</a></li>
    </ul>
    <ul class="footer-links policies">
      <li><a href="#">Terms of Service</a></li>
      <li><a href="#">Privacy Policy</a></li>
      <li><a href="#">Program Policies</a></li>
    </ul>
    <div class="footer-contact">
      Call : +47 53169027<br>
      info@mivolark.example
    </div>
    <address class="footer-address" style="font-style:normal">
      <h3>Contact Address</h3>
      <p>Mivo Lark AS,<br>Endodontic Teaching Center,<br>Tollbeks vei 41C<br>0397 Oslo, Norway.</p>
    </address>
    <div class="copyright">© 2012 MIVOLARK Copyright, All rights reserved</div>
  </footer>
</div>
</body>
</html>
```